business card deign

Logo needs the following on it.
1. attached logo
2. Tagline - "If it keeps a drink cold or the party going...we do it!"
3. Name- Dalton Pikes, Founder and CPO
4. Address - 412 E. Carver Avenue, Ste 2207, Tampa, FL. 33917
5. Phone - 555.318.4726

```html
<!DOCTYPE html>
<html lang="en">
<head>
<meta charset="UTF-8">
<title>Brindle Business Card</title>
<link href="https://fonts.googleapis.com/css2?family=Roboto:wght@400;500;700&display=swap" rel="stylesheet">
<style>
  :root {
    --backdrop: #222222;
    --card: #ecedea;
    --ink: #111111;
    --map-tone: #d6d7d3;
    --panel-shadow: rgba(0,0,0,0.22);
  }
  * { margin: 0; padding: 0; box-sizing: border-box; }
  html, body {
    width: 1200px; height: 711px; overflow: hidden;
    background: var(--backdrop);
    font-family: "Roboto", sans-serif;
    color: var(--ink);
  }
  .stage {
    position: relative; width: 1200px; height: 711px;
    display: flex; align-items: center; justify-content: center; gap: 40px;
  }
  .card {
    position: relative;
    width: 520px; height: 300px;
    background: var(--card);
    border-radius: 22px;
    overflow: hidden;
    box-shadow: 0 10px 24px rgba(0,0,0,0.6);
  }
  /* front */
  .world-map {
    position: absolute; left: 40px; top: 40px; width: 440px; height: 200px;
    background: radial-gradient(ellipse at center, var(--map-tone) 0%, rgba(214,215,211,0.4) 55%, rgba(236,237,234,0) 80%);
  }
  .brand {
    position: absolute; left: 0; right: 0; top: 118px;
    display: flex; align-items: center; justify-content: center; gap: 18px;
  }
  .brand-dot {
    width: 40px; height: 40px; border-radius: 50%; background: var(--ink);
  }
  .brand-name {
    font-weight: 700; font-size: 46px; letter-spacing: 14px;
  }
  /* back */
  .contact-panel {
    position: absolute; left: 258px; top: 0; right: 0; height: 190px;
    background: var(--card);
    box-shadow: -14px 10px 22px var(--panel-shadow);
  }
  .person {
    position: absolute; left: 60px; top: 118px; width: 190px; text-align: right;
  }
  .person-name { font-weight: 700; font-size: 26px; line-height: 1.1; }
  .person-role { font-size: 15px; margin-top: 2px; }
  .contact-list {
    position: absolute; left: 290px; top: 62px; list-style: none;
    font-size: 12.5px; line-height: 1.35;
  }
  .contact-list li { display: flex; gap: 6px; align-items: flex-start; margin-bottom: 3px; }
  .contact-list svg { width: 11px; height: 11px; margin-top: 2px; flex: none; }
  .tagline {
    position: absolute; right: 32px; bottom: 44px; font-size: 13px; font-weight: 500;
  }
</style>
</head>
<body>
<main class="stage">
  <section class="card card-front">
    <div class="world-map" role="img" aria-label="Faint dotted world map decoration"></div>
    <div class="brand">
      <span class="brand-dot"></span>
      <span class="brand-name">BRINDLE</span>
    </div>
  </section>

  <section class="card card-back">
    <div class="contact-panel"></div>
    <div class="person">
      <p class="person-name">Dalton Pikes</p>
      <p class="person-role">Founder and CPO</p>
    </div>
    <ul class="contact-list">
      <li>
        <svg viewBox="0 0 24 24"><path fill="currentColor" d="M6.6 10.8a15.1 15.1 0 0 0 6.6 6.6l2.2-2.2a1 1 0 0 1 1-.25 11.4 11.4 0 0 0 3.6.57 1 1 0 0 1 1 1V20a1 1 0 0 1-1 1A17 17 0 0 1 3 4a1 1 0 0 1 1-1h3.5a1 1 0 0 1 1 1c0 1.25.2 2.45.57 3.57a1 1 0 0 1-.25 1z"/></svg>
        <span>555.318.4726</span>
      </li>
      <li>
        <svg viewBox="0 0 24 24"><path fill="currentColor" d="M12 2a7 7 0 0 0-7 7c0 5.2 7 13 7 13s7-7.8 7-13a7 7 0 0 0-7-7zm0 9.5A2.5 2.5 0 1 1 12 6.5a2.5 2.5 0 0 1 0 5z"/></svg>
        <span>412 E. Carver Avenue,<br>Ste 2207, Tampa, FL. 33917</span>
      </li>
    </ul>
    <p class="tagline">If it keeps a drink cold or the party going...we do it!</p>
  </section>
</main>
</body>
</html>
```